Expedition Cruise Sales Website for the Polar Regions (Antarctica & Arctic)

This will be a website for selling cruises.
This site should have a homepage, a ship page, destinations, and itineraries.
I have created a file specifying each page, and it is attached.
Pages:
1. Home
2. Cruise Lines
- 2.1 Ships
3. Destinations
- 3.1 Region - 3.2 Country - 3.3 City
4. Itineraries
- 4.1 Itinerary
5. Blog / Travel Tips 6. About Us
7. Contact
Please take a look on the attached pdf
Target Market(s)
Expedition Travelers
Coding
Coded - Design and coding required
Number of Pages Required
5+ page
Font styles to use
Look and feel
Each slider illustrates characteristics of the customer's brand and the style your logo design should communicate.

```html
<!DOCTYPE html>
<html lang="en">
<head>
<meta charset="utf-8">
<title>Polarvia.co – Explore The World In Luxury At Sea</title>
<link href="https://fonts.googleapis.com/css2?family=Plus+Jakarta+Sans:wght@300;400;500;600;700&display=swap" rel="stylesheet">
<style>
:root{
  --brand:#2f6db5;
  --brand-bright:#1f7ae0;
  --ink:#1d1d1f;
  --muted:#6b6b70;
  --line:#c9ced6;
  --white:#ffffff;
  --hero-a:#0c2f4c;
  --hero-b:#1f5f86;
  --band:#3a72b6;
}
*{box-sizing:border-box;margin:0;padding:0}
html,body{width:1200px;height:4184px;overflow:hidden}
body{position:relative;font-family:"Plus Jakarta Sans",sans-serif;color:var(--ink);background:var(--white)}
.abs{position:absolute}
a{color:inherit;text-decoration:none}

/* hero */
.hero{left:0;top:0;width:1200px;height:802px;background:linear-gradient(180deg,#0b2c4d 0%,#1c4f73 40%,#2d6f8f 62%,#123a58 100%)}
.brand{display:flex;flex-direction:column;align-items:center;gap:8px;color:var(--white);font-weight:600;font-size:26px}
.brand-dot{width:34px;height:34px;border-radius:50%;background:currentColor}
.nav{left:338px;top:58px;display:flex;gap:17px;color:var(--white);font-size:19px;font-weight:500}
.nav-line{left:341px;top:104px;width:782px;height:1px;background:rgba(255,255,255,.45)}
.nav-active{left:341px;top:102px;width:54px;height:3px;background:var(--white)}
.hero h1{left:77px;top:466px;width:620px;color:var(--white);font-size:54px;line-height:62px;font-weight:700}
.hero p.lead{left:77px;top:610px;width:610px;color:var(--white);font-size:19px;line-height:24px}
.slide-no{color:var(--white);font-size:64px;font-weight:300;line-height:1}
.slide-rail{left:1118px;top:250px;width:3px;height:210px;background:rgba(255,255,255,.35)}
.slide-rail span{display:block;width:3px;height:80px;background:var(--white)}

/* section heads */
.sec-title{left:0;width:1200px;text-align:center;color:var(--brand);font-size:25px;font-weight:600;text-transform:uppercase}
.sec-text{left:240px;width:720px;text-align:center;font-size:15.5px;line-height:20px;color:var(--ink)}

/* tabs */
.tabs{left:214px;top:1024px;width:772px;display:flex;justify-content:space-between;font-size:17px;color:var(--muted)}
.tabs .on{color:var(--brand)}
.tab-line{left:214px;top:1064px;width:772px;height:2px;background:var(--line)}
.tab-line span{display:block;width:218px;height:3px;background:var(--brand)}

/* offers */
.offer{color:var(--white)}
.offer h3{position:absolute;left:24px;top:40px;font-size:23px;line-height:29px;font-weight:500}
.offer-main{left:77px;top:1112px;width:444px;height:650px;background:linear-gradient(180deg,#1d57b8 0%,#2a6fd6 45%,#1b4fa8 100%)}
.offer-main h3{left:14px;top:60px}
.offer-main .get{position:absolute;right:38px;top:30px;font-size:11px;display:flex;align-items:center;gap:6px}
.offer-main p{position:absolute;left:14px;top:522px;width:410px;font-size:15.5px;line-height:20px;font-weight:500}
.offer-a{left:520px;top:1146px;width:604px;height:292px;background:linear-gradient(160deg,#23384f 0%,#4a6a85 50%,#1b2c3f 100%)}
.offer-b{left:520px;top:1438px;width:604px;height:292px;background:linear-gradient(160deg,#0c2440 0%,#1f8a9a 45%,#5fd1c4 60%,#0b2b4a 100%)}

/* destinations band */
.dest-band{left:0;top:1878px;width:1200px;height:422px;background:linear-gradient(90deg,#5a7590 0%,#9fb0c2 45%,#c9b7c6 100%)}
.dest-band h2{left:77px;top:1970px;color:var(--white);font-size:23px;font-weight:700}
.dest-band p{left:77px;top:2010px;width:315px;color:var(--white);font-size:15px;line-height:20px}
.btn{left:77px;top:2152px;width:160px;height:50px;border-radius:4px;background:var(--brand-bright);color:var(--white);font-size:15.5px;font-weight:600;display:flex;align-items:center;justify-content:center}
.dest-card{top:1934px;width:222px;height:327px;color:var(--white);font-size:14.5px;font-weight:600;line-height:19px;text-align:center;display:flex;align-items:flex-end;justify-content:center;padding:0 10px 18px}

/* routes */
.route{top:2556px;width:198px;height:250px}
.route .label{position:absolute;left:32px;right:0;bottom:0;height:52px;background:var(--white);padding:8px 10px}
.route b{display:block;font-size:10px;font-weight:600;margin-bottom:3px}
.route i{display:block;font-style:normal;font-size:5.5px;line-height:7px;color:var(--muted)}

/* testimonials */
.quote{border:2px solid #b9cbe6;border-radius:8px;background:var(--white);text-align:center}
.quote .who{position:absolute;display:flex;align-items:center;text-align:left}
.avatar{border-radius:50%;background:linear-gradient(135deg,#8a6a55,#c9a88e)}
.stars{color:#f2a516;letter-spacing:2px}
.dots{left:514px;top:3543px;display:flex;gap:16px}
.dots span{width:15px;height:15px;border-radius:50%;background:#d4d4d8}
.dots span.on{background:var(--brand)}

/* newsletter */
.news{left:0;top:3620px;width:1200px;height:170px;background:var(--band);color:var(--white)}
.news h2{position:absolute;left:77px;top:48px;font-size:30px;font-weight:400}
.news p{position:absolute;left:77px;top:96px;width:500px;font-size:14px;line-height:20px;color:rgba(255,255,255,.7)}
.news .cta{position:absolute;left:878px;top:88px;font-size:24px;display:flex;align-items:center;gap:26px}

/* footer */
.foot-brand{left:140px;top:3842px;color:var(--brand);font-size:30px;font-weight:600;flex-direction:column}
.foot-about{left:84px;top:3954px;width:380px;font-size:13.5px;line-height:20px}
.foot-h{font-size:19px;font-weight:600}
.links{left:566px;top:3905px;list-style:none;font-size:18.5px;line-height:30px}
.social{left:862px;top:3919px;display:flex;gap:46px}
.social span{width:18px;height:18px;border-radius:50%;background:var(--ink)}
.field{left:849px;top:3972px;width:254px;height:30px;border:1px solid #9fb6d8;border-radius:3px;font-size:7px;color:var(--muted);display:flex;align-items:center;padding-left:30px}
.sub{left:1053px;top:3990px;width:70px;height:21px;background:var(--brand-bright);color:var(--white);font-size:6px;font-weight:700;display:flex;align-items:center;justify-content:center}
.rule{left:84px;top:4108px;width:1042px;height:1px;background:#555}
.copy{left:0;top:4144px;width:1200px;text-align:center;font-size:12px;font-weight:600}
</style>
</head>
<body>

<!-- hero -->
<section class="abs hero" role="img" aria-label="Cruise ship docked beside a harbour terminal at dusk with city towers behind"></section>
<div class="abs brand" style="left:76px;top:30px;"><span class="brand-dot"></span>Polarvia.co</div>
<nav class="abs nav"><a>Home</a><a>Cruise Lines</a><a>Destinations</a><a>Itineraries</a><a>Blog / Travel Tips</a><a>About Us</a><a>Contact</a></nav>
<div class="abs nav-line"></div><div class="abs nav-active"></div>
<div class="abs slide-no" style="left:1037px;top:272px;">01</div>
<div class="abs slide-no" style="left:1044px;top:372px;opacity:.45">02</div>
<div class="abs slide-no" style="left:1052px;top:494px;opacity:.2">03</div>
<div class="abs slide-rail"><span></span></div>
<section class="hero" style="background:none;position:absolute;left:0;top:0;width:1200px;height:802px">
  <h1 class="abs">Explore The World In Luxury At Sea</h1>
  <p class="abs lead">Enjoy An Unforgettable Cruise Experience With Exotic Destinations, Premium Services And Special Offers. Find Your Dream Trip And Embark On An Extraordinary Adventure Aboard A Luxury Cruise Ship!</p>
</section>

<!-- featured offers -->
<h2 class="abs sec-title" style="top:868px;">Featured Offers Section</h2>
<p class="abs sec-text" style="top:918px;">Find The Best Deals For Your Dream Sea Voyage! We Present A Variety Of Exclusive Cruise Packages With Special Prices, Luxurious Facilities, And The Best Routes In The World. Don't Miss The Opportunity To Explore The Beauty Of The Ocean With The Best Promos</p>
<div class="abs tabs"><span class="on">Best Cruises To Antarctica</span><span>Most Popular Cruises To Galápagos</span><span>Last Minute Deals</span></div>
<div class="abs tab-line"><span></span></div>

<article class="abs offer offer-main" role="img" aria-label="Expedition ship sailing among ice floes under a blue sky">
  <span class="get">Get Now
    <svg width="30" height="14" viewBox="0 0 30 14"><path d="M1 7h27M22 1l6 6-6 6" stroke="#fff" stroke-width="1.5" fill="none"/></svg></span>
  <h3>Last-Minute Deal –<br>Save $350</h3>
  <p>Experience An Exclusive Cruise To The Edge Of The World On A Luxury Cruise Ship. Enjoy Spectacular Views Of Icebergs, Penguin Encounters, And Premium Service Throughout The Journey.</p>
</article>
<article class="abs offer offer-a" role="img" aria-label="Red-hulled icebreaker moving through broken sea ice"><h3>Group Saver – 30% Off<br>For 4 Or More People</h3></article>
<article class="abs offer offer-b" role="img" aria-label="Small ship under green northern lights over polar ice"><h3>Early Bird Special<br>– 25% Discount</h3></article>

<!-- top destinations -->
<section class="abs dest-band" role="img" aria-label="Cruise ship bow on calm water at sunset"></section>
<h2 class="abs dest-band" style="background:none;left:77px;top:1970px;width:auto;height:auto;color:#fff;font-size:23px;font-weight:700">TOP DESTINATIONS</h2>
<p class="abs" style="left:77px;top:2010px;width:315px;color:#fff;font-size:15px;line-height:20px">Explore The World On A Luxury Cruise To The Best Destinations! From Majestic Glaciers To Exotic Tropical Islands, Each Voyage Offers An Unforgettable Experience.</p>
<a class="abs btn">Learn More</a>
<div class="abs dest-card" style="left:431px;background:linear-gradient(180deg,#1d3a4a,#2f6f6a 45%,#15242f)" role="img" aria-label="Northern lights over a snowy lake shore">Antarctica – Wonder At<br>The End Of The World</div>
<div class="abs dest-card" style="left:667px;background:linear-gradient(180deg,#3f5b3a,#5a7c49 45%,#43b3b8 70%,#2b4a3a)" role="img" aria-label="Aerial view of green islands around a turquoise lagoon">Galapagos Islands – A<br>Biodiversity Paradise</div>
<div class="abs dest-card" style="left:902px;background:linear-gradient(180deg,#5a86c4,#8fb2d8 35%,#2f5f8e 70%,#3a5a3a)" role="img" aria-label="Palm trees on a cliff above a Caribbean sea">Caribbean – Stunning<br>Tropical Beaches</div>

<!-- shipping routes -->
<h2 class="abs sec-title" style="top:2388px;">Shipping Route Highlights</h2>
<p class="abs sec-text" style="top:2438px;">Experience Extraordinary Ocean Voyages With A Wide Selection Of Exclusive Cruise Lines. From Polar Expeditions To Relaxing Tropical Getaways, We Offer Unforgettable Experiences With The Best Service.</p>
<div class="abs route" style="left:78px;background:linear-gradient(180deg,#7f8d9a,#d8dee4 50%,#f2f4f6)" role="img" aria-label="Snow-covered Antarctic mountains"><div class="label"><b>Antarctic Expedition</b><i>Sail past glaciers and meet penguin colonies on icy shores.</i></div></div>
<div class="abs route" style="left:287px;background:linear-gradient(180deg,#6ea0cf,#4a7a55 50%,#3cb9b2)" role="img" aria-label="Aerial view of a Galápagos island coastline"><div class="label"><b>Galápagos Islands Cruise</b><i>Discover rare wildlife across volcanic islands and clear bays.</i></div></div>
<div class="abs route" style="left:496px;background:linear-gradient(180deg,#2f5a3a,#3d7a55 45%,#6fc2c6)" role="img" aria-label="Tropical resort with palms and pools"><div class="label"><b>Luxury Caribbean Travel</b><i>Relax on white beaches and swim in warm turquoise water.</i></div></div>
<div class="abs route" style="left:705px;background:linear-gradient(180deg,#4f86c8,#a8c5e4 45%,#8a9aa8)" role="img" aria-label="Harbour with yachts and old city buildings"><div class="label"><b>European Cities Cruise</b><i>Visit historic ports, grand old towns and lively harbours.</i></div></div>
<div class="abs route" style="left:914px;background:linear-gradient(180deg,#8b7fa8,#c9b7d4 45%,#e8e6ef)" role="img" aria-label="Snowy Alaskan forest with a hiker"><div class="label"><b>Spectacular Alaskan Exploration</b><i>Hike snowy forests and watch whales in wild northern fjords.</i></div></div>

<!-- testimonials -->
<h2 class="abs sec-title" style="top:2930px;">Customer Testimonials</h2>
<p class="abs sec-text" style="top:2984px;">Hear Incredible Stories From Passengers Who Have Had Unforgettable Cruise Experiences With Us! From World-Class Service To Amazing Destinations, Here's Why Our Customers Choose To Cruise With Us Again And Again.</p>

<article class="abs quote" style="left:80px;top:3163px;width:270px;height:295px">
  <div class="who" style="left:16px;top:18px;gap:12px"><span class="avatar" style="width:56px;height:56px" role="img" aria-label="Customer portrait"></span><div><div style="font-size:15px;font-weight:600">btro</div><div style="font-size:10px">Lead Designer <span class="stars" style="font-size:12px">★★★★☆</span></div></div></div>
  <div style="position:absolute;left:0;right:0;top:112px;font-size:16px;font-weight:600">Absolutely stunning!</div>
  <div style="position:absolute;left:20px;right:20px;top:150px;font-size:10.5px;line-height:14px">I love the Coral Tide Dress! The fabric is premium, and the floral design is gorgeous.</div>
</article>
<article class="abs quote" style="left:408px;top:3089px;width:385px;height:407px">
  <div class="who" style="left:20px;top:34px;gap:14px"><span class="avatar" style="width:68px;height:68px" role="img" aria-label="Customer portrait"></span><div><div style="font-size:21px;font-weight:500">Ines</div><div style="font-size:15px">Lead Designer <span class="stars" style="font-size:20px;margin-left:16px">★★★★☆</span></div></div></div>
  <div style="position:absolute;left:0;right:0;top:140px;font-size:22px;font-weight:600">It was a very good experience</div>
  <div style="position:absolute;left:24px;right:24px;top:192px;font-size:16px;line-height:20px">What a trip! From start to finish, everything was perfect. Comfortable cabins, delicious food, and stunning views of Antarctica. Will definitely be back!</div>
</article>
<article class="abs quote" style="left:850px;top:3166px;width:270px;height:295px">
  <div class="who" style="left:16px;top:18px;gap:12px"><span class="avatar" style="width:56px;height:56px;background:linear-gradient(135deg,#222,#5a3a3a)" role="img" aria-label="Customer portrait"></span><div><div style="font-size:15px;font-weight:600">btra</div><div style="font-size:10px">Lead Designer <span class="stars" style="font-size:12px">★★★★☆</span></div></div></div>
  <div style="position:absolute;left:0;right:0;top:110px;font-size:16px;font-weight:600">High-quality and elegant.</div>
  <div style="position:absolute;left:30px;right:30px;top:150px;font-size:10.5px;line-height:14px">The Reef &amp; Tide Gift Set was the perfect gift—elegant, beautifully arranged, and truly unique!</div>
</article>
<svg class="abs" style="left:452px;top:3539px" width="20" height="22" viewBox="0 0 20 22"><path d="M14 2 5 11l9 9" stroke="#2f6db5" stroke-width="3" fill="none"/></svg>
<div class="abs dots"><span class="on"></span><span></span><span></span><span></span><span></span><span></span></div>
<svg class="abs" style="left:728px;top:3539px" width="20" height="22" viewBox="0 0 20 22"><path d="M6 2l9 9-9 9" stroke="#2f6db5" stroke-width="3" fill="none"/></svg>

<!-- newsletter -->
<section class="abs news">
  <h2>NEWSLETTER SUBSCRIPTION FORM</h2>
  <p>Jadilah yang pertama mendapatkan informasi tentang penawaran eksklusif, diskon spesial, dan destinasi terbaru langsung di kotak masuk Anda!</p>
  <a class="cta">Get consultation <svg width="24" height="16" viewBox="0 0 24 16"><path d="M1 8h21M16 2l6 6-6 6" stroke="#fff" stroke-width="2" fill="none"/></svg></a>
</section>

<!-- footer -->
<div class="abs brand foot-brand"><span class="brand-dot"></span>Polarvia.co</div>
<p class="abs foot-about">Polarvia.co is a marine expedition company that provides luxurious, safe and unforgettable cruise experiences to various exotic destinations around the world. With premium services, the best cruise ships and professional teams, we are committed to providing an extraordinary journey for every passenger.</p>
<div class="abs foot-h" style="left:566px;top:3848px">Quick Links:</div>
<ul class="abs links"><li>Home</li><li>Cruise Lines</li><li>Destination</li><li>Intineraries</li><li>Blog/Travel Tips</li><li>About Us</li><li>Contact</li></ul>
<div class="abs foot-h" style="left:858px;top:3848px;font-size:22px">Follow Us:</div>
<div class="abs social"><span></span><span></span><span></span><span></span></div>
<div class="abs field">you@example.com</div>
<div class="abs sub">SUBSCRIBE</div>
<div class="abs rule"></div>
<div class="abs copy">Polarvia.co - All Rights Reserved. Copyright © 2025</div>

</body>
</html>
```